Contemporary Business card for Event Manager

Needed for my startup events company in Melbourne. Events I manage will be based within the fashion industry, sporting events, product launches etc. Not weddings or small dinner parties. Therfore I am after something professional and aimed at high end corporate market; but with the added emphasis on not being too conservative or boring. I am happy with a pop of colour e.g. yellow or copper foil.

Target Market(s)

fashion industry, design industry, high end sporting events e.g. Polo, Grand Prix, corporate clients,

Industry/Entity Type

Fashion

Contact Information for Business Card

side 1
Lucy Brandt (can be upper or lower case, have a feature full stop between first and surname, or at the end of the nameetc) I am open to ideas. I would also be fine with my initials or name as a logo on the front (if this is the case my full name would need to go on the second side of the card.
2nd side:
Mobile: +61 400 817 263
email: lucy.brandt@mailnest.com.au

on one side of the card:
event management | brand activation | Advisory Services

Font styles to use
Serif
Sans Serif

Requirements
Must have
• side 2 must have
• mobile number
• email address
• event management | brand activation | Advisory Services
• ** my full name (Lucy Brandt) must be on the card somewhere)
Nice to have
• 1st side
• I see the card stock being either a dark grey, light grey, natural white or black (all matt colours on unprocessed card). I see the writing being copper foil, or foil white or foil black.
• To give you a feel for me, think: contemporary, minimalist, I love line drawings, concrete, white with grey vein marble, copper, white, grey, black...yes I do like colour....yellow (but pops of colour) ;) I would like the card to look designer but 'on trend' as I deal with a lot of design and fashion clients....styles - think the sophistication and simplicity of Vireaux or urban contemporary.
• some examples of what I like. Although please don't leet this limit you...I really am happy to have something a little more urban or design focused like a line drawing of an object, person too or a photo image too.
• https://www.moodtackle.com/pin/830165427719302846/
• https://www.moodtackle.com/pin/607281935540173268/
• https://www.moodtackle.com/pin/318746205913457092/
• https://www.moodtackle.com/pin/41983627530918476/
• https://www.moodtackle.com/pin/53128940672419087/
• https://www.moodtackle.com/pin/90316284750638152/
• https://www.moodtackle.com/pin/734092618450362918/
• https://www.moodtackle.com/pin/926354081736215407/
• https://www.moodtackle.com/pin/481627093518704356/
Should not have
• should not look commercial or have cartoonish looking logos. However happy with a simple line drawing or logo with initials etc.

```html
<!DOCTYPE html>
<html lang="en">
<head>
<meta charset="utf-8">
<title>Lucy Brandt — Business Card</title>
<link rel="stylesheet" href="https://fonts.googleapis.com/css2?family=Questrial&family=Jost:wght@300&display=swap">
<style>
  :root {
    --backdrop: #e9e6e3;
    --card-black: #0c0c0d;
    --card-pink: #e8197f;
    --card-pink-deep: #c8166e;
    --rule-white: #ffffff;
    --ink-white: #ffffff;
  }
  * { margin: 0; padding: 0; box-sizing: border-box; }
  html, body { width: 1200px; height: 892px; overflow: hidden; }
  body {
    background: var(--backdrop);
    display: flex;
    flex-direction: column;
    align-items: center;
    justify-content: center;
    gap: 40px;
  }
  .card {
    position: relative;
    width: 620px;
    height: 354px;
    border-radius: 26px;
    overflow: hidden;
    box-shadow: 0 10px 26px rgba(0,0,0,.22);
    display: flex;
  }
  .band { height: 100%; }
  .band--side { width: 92px; flex: none; }
  .band--centre { flex: 1; position: relative; }
  .rule { width: 3px; flex: none; background: var(--rule-white); }

  .card--front .band--side { background: var(--card-pink); }
  .card--front .band--centre {
    background: linear-gradient(160deg, #222 0%, var(--card-black) 45%, #000 100%);
  }
  .card--back .band--side { background: var(--card-black); }
  .card--back .band--centre {
    background: linear-gradient(170deg, var(--card-pink) 0%, #e0408f 50%, var(--card-pink-deep) 100%);
  }

  .name {
    position: absolute;
    inset: 0;
    display: flex;
    align-items: center;
    justify-content: center;
    font-family: "Jost", sans-serif;
    font-weight: 300;
    font-size: 38px;
    letter-spacing: 1px;
    color: var(--ink-white);
    text-transform: uppercase;
  }
  .details {
    position: absolute;
    left: 78px;
    top: 62px;
    font-family: "Questrial", sans-serif;
    color: var(--ink-white);
    font-size: 21px;
    line-height: 1.3;
    letter-spacing: .5px;
  }
  .contact { margin-bottom: 52px; }
  .services { padding-left: 68px; }
</style>
</head>
<body>
  <section class="card card--front" aria-label="Card front">
    <div class="band band--side"></div>
    <div class="rule"></div>
    <div class="band band--centre">
      <h1 class="name">Lucy.Brandt</h1>
    </div>
    <div class="rule"></div>
    <div class="band band--side"></div>
  </section>

  <section class="card card--back" aria-label="Card back">
    <div class="band band--side"></div>
    <div class="rule"></div>
    <div class="band band--centre">
      <div class="details">
        <p class="contact">+61 400 817 263<br>lucy.brandt@mailnest.com.au</p>
        <p class="services">event management<br>brand activation<br>Advisory Services</p>
      </div>
    </div>
    <div class="rule"></div>
    <div class="band band--side"></div>
  </section>
</body>
</html>
```